Probate (Legal) Wordpress Design with Coding for Online Company

I need a Wordpress design with coding, pictures, content to be provided by me, fully responsive, and development. This is for a 6-7 page design.

Pages Needed: Home/About/Probate/Process/FAQ/Contact Us/Blog.

The home page should be organized as followed:
-Steps in Probate: Gather; Implement; Close (each step will come with content)
-Flat-Fee Price & Savings: Content will go here with a button to contact us (phone number) or just the phone number.
-You Have Questions, We Have Answers: five questions with content. Only one question answer to show at a time when clicked on the question from the list.
-Get to Know Us: a brief description with content about what we do and who we are.

Main image slogan: Helping Californians deal with loss with DIGNITY & UNDERSTATING (you may use a better slogan if you wish).

The Contact page should not have a map since we are an online company. We service the entire state of California in every county and city.

The About page should be simple, direct, and easy on the eye. It should have a brief description of who we are and it should have no more than 6 reasons why the client should hire us.

About our online California company. We are not attorneys but legal document assistants who prepare legal documents for probate estate when someone dies with or without a will and assets need to be distributed. We have a flat-fee for Formal Probate of $999 and $699 for Informal Probate. We are an online company and offer our services to the entire state of California in every county. We do everything over the phone and email. The turn around time for us to prepare the initial legal paperwork for the client is within 3-5 business days. We can prepare, file, serve and manage a probate matter from petition to closing. We are not attorneys so our prices are very affordable compare to the attorney.

The company name for the website will be www.velmarhollow.com, The Velmar Hollow Group.

I do not have a logo yet. The colors of the website should be easy on the eye and calming. THE SITE SHOULD BE SIMPLE AND STRAIGHT TO THE POINT. EASY TO NAVIGATE.

The company phone number should be very visible and should stand out to the client. It should also be clickable and ready to dial for smartphone users.

I do not want a contact form on the homepage. THE MAIN THING IS FOR THE POTENTIAL CLIENT TO CALL OUR OFFICE TO SIGN UP.

I do like some images of family or people since we are dealing with people who just lost a loved one. Not all the images have to be of people.

The site should not look like we practice law or that people can mistake us for attorneys.

Target Market(s)

People who just lost a loved one who had property, assets, in California but died with or without a will or trust. This is for people looking to hire non-attorneys.

Coding

Coded - Design and coding required

Font styles to use
Serif

Colors

Designer to choose colors to be used in the design.

Requirements
Must have
• Refer to Project Description.
Nice to have
• The sample images provided is what I am attracted to for the homepage image.
Should not have

```html
<!DOCTYPE html>
<html lang="en">
<head>
<meta charset="utf-8">
<title>The Velmar Hollow Group — Probate Document Help</title>
<link rel="stylesheet" href="https://fonts.googleapis.com/css2?family=Poppins:wght@400;500;600;700&display=swap">
<style>
  :root{
    --ink:#1c1c28;
    --muted:#7a7a86;
    --royal:#1f2dbf;
    --navy:#0f1547;
    --heading:#3a4a8c;
    --rule:#9aa6e6;
    --pale:#f2f2f4;
    --row:#b8c2fb;
    --white:#ffffff;
  }
  *{box-sizing:border-box;margin:0;padding:0}
  html,body{width:1200px;height:2941px;overflow:hidden;background:var(--white)}
  body{font-family:"Poppins",sans-serif;color:var(--ink);position:relative}
  .section{position:absolute;left:0;width:1200px}
  .abs{position:absolute}
  .section-title{position:absolute;left:0;width:100%;text-align:center;font-weight:600;color:var(--heading);font-size:30px}
  .title-rule{position:absolute;left:50%;width:196px;margin-left:-98px;height:2px;background:var(--rule)}

  /* header + hero */
  .hero{top:0;height:506px;background:var(--pale)}
  .hero-photo{position:absolute;left:470px;top:0;width:730px;height:506px;
    background:radial-gradient(ellipse at 55% 45%,#e9d3c4 0%,#d7c0b4 30%,#c7ced8 60%,#eef0f3 85%)}
  .brand{position:absolute;left:106px;top:38px;font-size:31px;font-weight:600;color:var(--royal)}
  .nav{position:absolute;top:45px;left:520px;display:flex;gap:0;font-size:14px}
  .nav a{color:var(--ink);text-decoration:none;position:absolute;white-space:nowrap}
  .nav .current::after{content:"";position:absolute;left:0;right:0;bottom:-10px;height:2px;background:var(--rule)}
  .hero-kicker{position:absolute;left:106px;top:202px;font-size:15px;font-weight:500}
  .hero-headline{position:absolute;left:104px;top:220px;color:var(--royal);font-weight:700;line-height:1}
  .hero-headline .l1{display:block;font-size:54px}
  .hero-headline .l2{display:block;font-size:37px;margin-top:6px}
  .btn{display:flex;align-items:center;justify-content:center;border-radius:4px;color:var(--white);font-weight:600;text-decoration:none}
  .btn-navy{background:var(--navy)}
  .btn-royal{background:var(--royal)}
  .hero-btn{position:absolute;left:106px;top:343px;width:194px;height:49px;font-size:15px}
  .dots{position:absolute;left:106px;top:440px;display:flex;gap:12px}
  .dots span{width:7px;height:7px;border-radius:50%;background:#c4c6cf}
  .dots span.on{background:var(--heading)}

  /* steps */
  .steps{top:506px;height:451px;background:var(--white)}
  .step{position:absolute;top:140px;width:320px;text-align:center}
  .step svg{display:block;margin:0 auto}
  .step h3{font-size:15px;font-weight:500;margin-top:24px}
  .step p{font-size:10.5px;line-height:21px;color:var(--muted);margin-top:18px}

  /* flat fee */
  .fee{top:957px;height:459px;background:linear-gradient(160deg,#5b6b97 0%,#4a5a86 45%,#3c4a70 100%);color:var(--white);text-align:center}
  .fee-photo{position:absolute;inset:0;background:radial-gradient(ellipse at 62% 40%,rgba(120,140,190,.55),transparent 60%),linear-gradient(180deg,rgba(80,95,140,.35),rgba(70,85,80,.45))}
  .fee h2{position:absolute;top:82px;width:100%;font-size:30px;font-weight:600}
  .fee p{position:absolute;top:180px;left:270px;width:660px;font-size:12.5px;line-height:23px}
  .fee .phone{position:absolute;top:265px;width:100%;font-size:44px;font-weight:600;color:var(--white);text-decoration:none;letter-spacing:1px;display:block}
  .fee-btn{position:absolute;left:478px;top:337px;width:234px;height:53px;font-size:15px}

  /* faq */
  .faq{top:1416px;height:760px;background:var(--white)}
  .faq-card{position:absolute;left:167px;top:185px;width:860px;height:530px;background:#f5f5f7;border:1px solid #e8e8ec;border-radius:4px}
  .faq-row{position:absolute;left:24px;width:812px;height:59px;border-radius:4px;background:var(--row);display:flex;align-items:center;font-size:15px;color:var(--ink)}
  .faq-row.open{background:var(--navy);color:var(--white)}
  .q-badge{width:44px;height:44px;margin:0 18px 0 8px;border-radius:4px;background:var(--navy);color:var(--white);display:flex;align-items:center;justify-content:center;font-size:13px;font-weight:600}
  .faq-row.open .q-badge{background:var(--row);color:var(--navy)}
  .faq-row svg{position:absolute;right:22px;top:22px}
  .faq-answer{position:absolute;left:48px;top:95px;width:770px}
  .faq-answer h4{font-size:14px;font-weight:600}
  .faq-answer p{font-size:12px;line-height:23px;color:var(--muted);margin-top:18px}

  /* know us */
  .know{top:2176px;height:696px;background:var(--pale)}
  .know-card{position:absolute;top:155px;width:474px;height:486px;background:var(--white)}
  .know-photo{height:211px}
  .know-card h3{position:absolute;left:27px;top:254px;font-size:19px;font-weight:600;color:var(--heading)}
  .know-card p{position:absolute;left:27px;top:300px;width:425px;font-size:12px;line-height:22px;color:var(--muted)}
  .know-btn{position:absolute;left:27px;top:415px;width:149px;height:36px;font-size:14px}

  /* footer */
  .footer{top:2872px;height:69px;background:var(--white)}
  .footer .brand{top:20px;font-size:22px}
  .footer small{position:absolute;right:78px;top:28px;font-size:10.5px;color:var(--muted)}
</style>
</head>
<body>

<section class="section hero">
  <div class="hero-photo" role="img" aria-label="Photo of a smiling family: mother, father and young son hugging"></div>
  <div class="brand">The Velmar Hollow Group</div>
  <nav class="nav">
    <a class="current" style="left:0">Home</a>
    <a style="left:83px">About</a>
    <a style="left:163px">Probate</a>
    <a style="left:258px">Process</a>
    <a style="left:352px">FAQ</a>
    <a style="left:420px">Contact Us</a>
    <a style="left:537px">Blog</a>
  </nav>
  <p class="hero-kicker">Helping Californians deal with loss with</p>
  <h1 class="hero-headline"><span class="l1">DIGNITY &amp;</span><span class="l2">UNDERSTATING</span></h1>
  <a class="btn btn-navy hero-btn">LEARN MORE</a>
  <div class="dots"><span class="on"></span><span></span><span></span><span></span></div>
</section>

<section class="section steps">
  <h2 class="section-title" style="top:52px">Steps in Probate</h2>
  <div class="title-rule" style="top:104px"></div>

  <div class="step" style="left:101px">
    <svg width="54" height="40" viewBox="0 0 54 40" fill="none" stroke="var(--heading)" stroke-width="2" stroke-linejoin="round" stroke-linecap="round">
      <path d="M2 14 L12 6 L22 12 L30 8 L42 10 L52 20"/>
      <path d="M12 20 L24 32 Q28 35 31 31 L42 20" stroke="#3d8fd6"/>
      <path d="M22 12 L16 18 Q19 22 24 18 L28 16"/>
      <path d="M2 14 L12 24"/>
    </svg>
    <h3>Gather</h3>
    <p>Sed ut perspiciatis unde omnis iste natus error sit voluptatem accusantium doloremque laudantium, totam rem aperiam, eaque ipsa quae ab illo inventore veritatis et quasi architecto beatae vitae dicta</p>
  </div>

  <div class="step" style="left:428px">
    <svg width="44" height="44" viewBox="0 0 44 44" fill="none" stroke="var(--navy)" stroke-width="2">
      <circle cx="22" cy="22" r="19"/>
      <rect x="16" y="11" width="12" height="20" rx="6"/>
      <line x1="22" y1="14" x2="22" y2="19" stroke="#3d8fd6"/>
    </svg>
    <h3>Implement</h3>
    <p>Sed ut perspiciatis unde omnis iste natus error sit voluptatem accusantium doloremque laudantium, totam rem aperiam, eaque ipsa quae ab illo inventore veritatis et quasi architecto beatae vitae dicta</p>
  </div>

  <div class="step" style="left:771px">
    <svg width="40" height="44" viewBox="0 0 40 44" fill="none" stroke="var(--navy)" stroke-width="2" stroke-linecap="round">
      <circle cx="20" cy="12" r="8"/>
      <path d="M5 42 V34 Q5 24 20 24 Q35 24 35 34 V42 Z"/>
      <rect x="15" y="32" width="10" height="8" rx="1" stroke="#3d8fd6"/>
      <path d="M17 32 V29 Q20 26 23 29 V32" stroke="#3d8fd6"/>
    </svg>
    <h3>Close</h3>
    <p>Sed ut perspiciatis unde omnis iste natus error sit voluptatem accusantium doloremque laudantium, totam rem aperiam, eaque ipsa quae ab illo inventore veritatis et quasi architecto beatae vitae dicta</p>
  </div>
</section>

<section class="section fee">
  <div class="fee-photo" role="img" aria-label="Photo of a father and two children playing in a flowering meadow, dimmed under a blue overlay"></div>
  <h2>Flat Fee Price &amp; Savings</h2>
  <p>Sed ut perspiciatis unde omnis iste natus error sit voluptatem accusantium doloremque laudantium, totam rem aperiam, eaque ipsa quae ab illo inventore veritatis et quasi architecto beatae vitae dicta sunt explicabo. Nemo enim ipsam voluptatem</p>
  <a class="phone" href="tel:18005550147">1-800-555-0147</a>
  <a class="btn btn-royal fee-btn" href="tel:18005550147">Contact Us</a>
</section>

<section class="section faq">
  <h2 class="section-title" style="top:90px">You Have Questions, We Have Answers</h2>
  <div class="title-rule" style="top:149px"></div>
  <div class="faq-card">
    <div class="faq-row open" style="top:20px">
      <span class="q-badge">Q</span>Sed ut perspiciatis unde omnis iste natus error sit voluptatem ?
      <svg width="14" height="14" viewBox="0 0 14 14" fill="none" stroke="#fff" stroke-width="2"><path d="M3 5 L7 9 L11 5"/></svg>
    </div>
    <div class="faq-answer">
      <h4>Answers</h4>
      <p>Sed ut perspiciatis unde omnis iste natus error sit voluptatem accusantium doloremque laudantium, totam rem aperiam, eaque ipsa quae ab illo inventore veritatis et quasi architecto beatae vitae dicta sunt explicabo. Nemo enim ipsam voluptatem quia voluptas sit aspernatur aut odit aut fugit, sed quia consequuntur magni dolores eos qui ratione voluptatem sequi nesciunt. Neque porro quisquam est, qui dolorem ipsum quia dolor sit amet</p>
    </div>
    <div class="faq-row" style="top:251px">
      <span class="q-badge"></span>At vero eos et accusamus et iusto odio dignissimos ducimus qui ?
      <svg width="14" height="14" viewBox="0 0 14 14" fill="none" stroke="#fff" stroke-width="2"><path d="M5 3 L9 7 L5 11"/></svg>
    </div>
    <div class="faq-row" style="top:316px">
      <span class="q-badge">Q</span>Et harum quidem rerum facilis est et expedita distinctio
      <svg width="14" height="14" viewBox="0 0 14 14" fill="none" stroke="#fff" stroke-width="2"><path d="M5 3 L9 7 L5 11"/></svg>
    </div>
    <div class="faq-row" style="top:381px">
      <span class="q-badge">Q</span>Perspiciatis unde omnis iste natus error sit voluptatem ?
      <svg width="14" height="14" viewBox="0 0 14 14" fill="none" stroke="#fff" stroke-width="2"><path d="M5 3 L9 7 L5 11"/></svg>
    </div>
    <div class="faq-row" style="top:446px">
      <span class="q-badge">Q</span>Debitis aut rerum necessitatibus saepe eveniet ut et voluptates ?
      <svg width="14" height="14" viewBox="0 0 14 14" fill="none" stroke="#fff" stroke-width="2"><path d="M5 3 L9 7 L5 11"/></svg>
    </div>
  </div>
</section>

<section class="section know">
  <h2 class="section-title" style="top:48px">Get to Know Us</h2>
  <div class="title-rule" style="top:104px"></div>

  <article class="know-card" style="left:108px">
    <div class="know-photo" role="img" aria-label="Photo of a team meeting around a table with laptops" style="background:linear-gradient(120deg,#cfc9c4,#9a9fa8 50%,#d9d4cf)"></div>
    <h3>What We Do ?</h3>
    <p>Sed ut perspiciatis unde omnis iste natus error sit voluptatem accusantium doloremque laudantium, totam rem aperiam, eaque ipsa quae ab illo inventore veritatis et quasi architecto beatae vitae dicta sunt explicabo. Nemo enim ipsam voluptatem.</p>
    <a class="btn btn-royal know-btn">Read More</a>
  </article>

  <article class="know-card" style="left:610px">
    <div class="know-photo" role="img" aria-label="Photo of a smiling multi-generation family together outdoors" style="background:linear-gradient(120deg,#e6b98f,#d49a74 45%,#f0d3b5)"></div>
    <h3>Who We Are ?</h3>
    <p>Sed ut perspiciatis unde omnis iste natus error sit voluptatem accusantium doloremque laudantium, totam rem aperiam, eaque ipsa quae ab illo inventore veritatis et quasi architecto beatae vitae dicta sunt explicabo. Nemo enim ipsam voluptatem.</p>
    <a class="btn btn-royal know-btn">Read More</a>
  </article>
</section>

<footer class="section footer">
  <div class="brand">The Velmar Hollow Group</div>
  <small>© 2017 Company Name | All Rights Reserved</small>
</footer>

</body>
</html>
```